RW Holloway LLC Business Card - Civil Engineering & Consulting Firm

We need a Business Card that is elegant, and masculine.  It is our Professional Civil Engineering & Consulting Company located in San Antonio TX (Not s construction or builder firm- no gears & no tool images please). We provide civil engineering services including  commercial site plans, grading and drainage plans, utility plans, hydraulics and hydrology, land planning, utility coordination, and other general civil engineering services related to commercial and residential development.
We have 2 existing Logos. We would like to convey reliability, strength, trustworthiness and attention to detail.  Blues and orange tones as per logo We are OK with the use of a darker blue in the mix.  We have 2 logo versions - Full Company Name Logo to go on the back of card, & Small Icon Logo for the front w/ personal Info.

Target Market(s)
Architects, Real Estate Developers, Other Strctural Engineers, Surveyers, General Contractors
Industry/Entity Type
Professional Civil Engineering
Contact Information for Business Card
Name, Position, Address, Cell & Office #, email, and company website
Font styles to use
Other font styles liked:
- Avian
Requirements
Should not have
- No Tools, No Gears, no Cranes, or Construction Equipment.

```html
<!DOCTYPE html>
<html lang="en">
<head>
<meta charset="utf-8">
<title>RW Holloway LLC Business Card</title>
<link href="https://fonts.googleapis.com/css2?family=Montserrat:wght@300;400;600;700&display=swap" rel="stylesheet">
<style>
  :root {
    --backdrop: #353535;
    --card: #161616;
    --card-edge: #7aa9d8;
    --sky: #7fb0e0;
    --amber: #f0962a;
    --ink: #f2f2f2;
    --pattern: #1e1e1e;
  }
  * { margin: 0; padding: 0; box-sizing: border-box; }
  html, body { width: 1200px; height: 801px; overflow: hidden; }
  body {
    background: var(--backdrop);
    font-family: "Montserrat", sans-serif;
    position: relative;
  }
  .card {
    position: absolute;
    top: 240px;
    width: 560px;
    height: 320px;
    background: var(--card);
    overflow: hidden;
    box-shadow: 0 14px 30px rgba(0,0,0,.45);
  }
  .card-front { left: 25px; }
  .card-back { left: 615px; border-bottom: 3px solid var(--card-edge); }

  .front-swoosh { position: absolute; left: 0; bottom: 0; width: 560px; height: 320px; }

  .brand {
    position: absolute;
    left: 34px;
    top: 92px;
    width: 220px;
  }
  .brand-name {
    color: var(--sky);
    font-weight: 300;
    font-size: 27px;
    letter-spacing: 2px;
    line-height: 1.15;
  }
  .brand-tagline {
    margin-top: 10px;
    color: var(--amber);
    font-size: 9px;
    letter-spacing: 4px;
    font-weight: 400;
  }
  .divider {
    position: absolute;
    left: 272px;
    top: 40px;
    width: 1px;
    height: 170px;
    background: var(--sky);
    opacity: .7;
  }
  .contact {
    position: absolute;
    left: 290px;
    top: 38px;
    color: var(--ink);
    font-size: 11.5px;
    line-height: 1.5;
  }
  .contact-name {
    color: var(--sky);
    font-weight: 700;
    font-size: 17px;
    letter-spacing: .5px;
    line-height: 1.2;
  }
  .contact-title { margin-bottom: 8px; }
  .contact-address { margin-bottom: 8px; }
  .contact-row { display: flex; align-items: center; gap: 7px; }
  .contact-row svg { width: 10px; height: 10px; flex: none; }

  .back-pattern {
    position: absolute;
    inset: 0;
    background: linear-gradient(135deg, #111 0%, var(--pattern) 55%, #262626 100%);
  }
  .back-mark {
    position: absolute;
    right: 60px;
    top: 140px;
    display: flex;
    align-items: center;
    gap: 8px;
    color: var(--amber);
    font-size: 14px;
    font-weight: 600;
    letter-spacing: 1px;
  }
  .back-mark span.dot {
    width: 10px; height: 10px; background: var(--sky);
  }
</style>
</head>
<body>

<section class="card card-front">
  <svg class="front-swoosh" viewBox="0 0 560 320" aria-hidden="true">
    <path d="M560 150 C 470 230, 350 270, 230 320 L560 320 Z" fill="var(--sky)"/>
    <path d="M560 140 C 460 225, 340 270, 220 320 L234 320 C 350 272, 470 232, 560 156 Z" fill="var(--amber)"/>
    <path d="M0 316 L560 316 L560 320 L0 320 Z" fill="var(--card-edge)"/>
  </svg>

  <div class="brand">
    <div class="brand-name">RW HOLLOWAY LLC</div>
    <div class="brand-tagline">CONSULTING ENGINEERS</div>
  </div>

  <div class="divider"></div>

  <div class="contact">
    <div class="contact-name">DANIEL MARSH</div>
    <div class="contact-title">President</div>
    <div class="contact-address">1180 Harbor Crest Way<br>Bay City CA 90417</div>
    <div class="contact-row">
      <svg viewBox="0 0 10 10"><rect x="2.5" y="0.5" width="5" height="9" rx="1" fill="none" stroke="var(--amber)" stroke-width="1.2"/></svg>
      555-310-4827
    </div>
    <div class="contact-row">
      <svg viewBox="0 0 10 10"><path d="M2 1 L4 1 L4.6 3.2 L3.4 4.2 C4 5.6 4.6 6.2 6 6.8 L7 5.6 L9 6.2 L9 8.2 C5 8.6 1.4 5 2 1 Z" fill="var(--amber)"/></svg>
      555-310-4827
    </div>
    <div class="contact-row">
      <svg viewBox="0 0 10 10"><rect x="0.5" y="2" width="9" height="6" fill="var(--amber)"/><path d="M0.5 2 L5 5.5 L9.5 2" fill="none" stroke="var(--card)" stroke-width="1"/></svg>
      info@rwhollowayconsulting.com
    </div>
    <div class="contact-row">
      <svg viewBox="0 0 10 10"><circle cx="5" cy="5" r="4.5" fill="var(--amber)"/><path d="M0.5 5 H9.5 M5 0.5 C3 3 3 7 5 9.5 M5 0.5 C7 3 7 7 5 9.5" fill="none" stroke="var(--card)" stroke-width=".7"/></svg>
      www.rwhollowayconsulting.com
    </div>
  </div>
</section>

<section class="card card-back">
  <div class="back-pattern" role="img" aria-label="Subtle dark embossed repeating brand pattern"></div>
  <div class="back-mark"><span class="dot"></span>RW Holloway LLC</div>
</section>

</body>
</html>
```